Webdesign für industrielle Produktion von Suppen, Saucen, Bouillons und Konzentraten
Zielgruppe
Industrielle Produktion von Suppen, Saucen, Bouillons und Konzentraten
Aufgabenstellung
Aufmachung nicht zu modern, eher klassisch Understatement

```html
<!DOCTYPE html>
<html lang="de">
<head>
<meta charset="utf-8">
<title>Velmora</title>
<link href="https://fonts.googleapis.com/css2?family=Poppins:wght@500;600;700&family=Inter:wght@400;500;600&display=swap" rel="stylesheet">
<style>
:root{
  --red:#d4151d;
  --red-dark:#6e080b;
  --ink:#111111;
  --muted:#555555;
  --card:#dadada;
  --white:#ffffff;
  --wood:#6b4429;
}
*{box-sizing:border-box;margin:0;padding:0}
html,body{width:1200px;height:3997px;overflow:hidden;background:var(--white)}
body{position:relative;font-family:'Inter',Arial,sans-serif;color:var(--ink)}
h1,h2,h3{font-family:'Poppins',Arial,sans-serif}

/* header */
.site-header{position:absolute;left:0;top:0;width:1200px;height:74px;background:var(--white);border-bottom:1px solid #e6e6e6;z-index:3}
.brand{position:absolute;left:60px;top:22px;display:flex;align-items:center;gap:10px;font-family:'Poppins',sans-serif;font-weight:600;font-size:28px;line-height:1;color:var(--red)}
.brand i{display:block;width:14px;height:14px;background:currentColor}
.main-nav{position:absolute;left:431px;top:44px;display:flex;gap:20px;font-size:13px;font-weight:500}
.main-nav a{color:var(--ink);text-decoration:none}
.main-nav a.active{color:var(--red);text-decoration:underline}
.header-icons{position:absolute;right:56px;top:42px;display:flex;gap:22px}

/* hero */
.hero{position:absolute;left:0;top:74px;width:1200px;height:649px;background:linear-gradient(180deg,#0d0b0a 0%,#231810 45%,var(--wood) 75%,#3a2415 100%)}
.hero-photo{position:absolute;left:690px;top:104px;width:370px;height:430px;border-radius:18px;background:linear-gradient(160deg,#f1e7d6 0%,#b91b1f 55%,#6a0c0d 100%);opacity:.85}
.hero h1{position:absolute;left:60px;top:140px;font-size:55px;line-height:81px;color:var(--white);font-weight:700}
.hero p{position:absolute;left:60px;top:312px;width:370px;font-size:13px;line-height:17px;color:var(--white)}
.btn{display:inline-flex;align-items:center;gap:8px;background:var(--red);color:var(--white);border-radius:22px;font-size:13px;font-weight:500;padding:0 20px;height:40px;box-shadow:0 4px 10px rgba(0,0,0,.3)}
.hero .btn{position:absolute;left:58px;top:392px}

.section-title{position:absolute;left:0;width:1200px;text-align:center;font-size:44px;font-weight:600;line-height:64px}

/* product cards */
.card{position:absolute;width:258px;background:var(--card);border-radius:14px;text-align:center}
.card.hot{background:linear-gradient(180deg,var(--red) 0%,var(--red-dark) 100%);color:var(--white)}
.card .shot{position:absolute;left:39px;top:-58px;width:180px;height:150px;border-radius:50% 50% 14px 14px;background:linear-gradient(180deg,#e8e8e8 0%,#c2191d 60%,#d8b24a 100%)}
.card h3{position:absolute;left:0;width:100%;top:106px;font-family:'Inter',sans-serif;font-size:17px;font-weight:600;line-height:24px}
.card .price{position:absolute;left:0;width:100%;top:168px;font-size:13px}
.card .rule{position:absolute;left:24px;right:24px;top:203px;height:2px;background:currentColor}
.card .rule::before,.card .rule::after{content:"";position:absolute;top:-3px;width:8px;height:8px;border-radius:50%;background:currentColor}
.card .rule::before{left:-2px}.card .rule::after{right:-2px}
.card .more{position:absolute;left:0;width:100%;top:222px;font-size:13px;font-weight:500}

/* banner */
.banner{position:absolute;left:0;top:1687px;width:1200px;height:374px;background:linear-gradient(90deg,#2a2a2a 0%,#1b1b1b 55%,#111 100%)}
.banner-photo{position:absolute;left:690px;top:20px;width:470px;height:334px;border-radius:50%;background:radial-gradient(circle at 60% 45%,#d94b1f 0%,#a52b12 35%,#2d2520 70%,transparent 72%)}
.banner h2{position:absolute;left:60px;top:92px;font-size:44px;line-height:64px;color:var(--white);font-weight:700}
.banner .btn{position:absolute;left:60px;top:249px;height:36px}

/* tabs */
.shop-label{position:absolute;left:0;width:1200px;top:2260px;text-align:center;font-size:17px;font-weight:500}
.tabs{position:absolute;left:354px;top:2300px;display:flex;align-items:center;gap:18px;font-size:13px}
.tab{padding:6px 32px;border:1.5px solid var(--red);border-radius:8px}
.dot-sep{width:6px;height:20px;display:flex;flex-direction:column;align-items:center;justify-content:space-between}
.dot-sep i{display:block;width:6px;height:6px;border-radius:50%;background:var(--red)}

.card.wide{text-align:left}
.card.wide .shot{left:55px;top:-56px;background:linear-gradient(180deg,#e6e6e6 0%,#3d8a3a 45%,#c8a23a 100%)}
.card.wide h3{left:23px;top:120px;font-size:18px}
.card.wide .desc{position:absolute;left:23px;top:150px;width:205px;font-size:13px;line-height:16px}
.card.wide .price{left:23px;top:235px;width:auto;font-weight:500}
.card.wide .rule{left:23px;right:58px;top:268px}
.card.wide .more{left:23px;top:301px;width:auto}

/* testimonials */
.quote{position:absolute;background:#efefef;border-radius:6px;text-align:center}
.quote.main{background:linear-gradient(180deg,var(--red) 0%,#7a090c 100%);color:var(--white)}
.avatar{position:absolute;border-radius:50%;background:linear-gradient(180deg,#9aa3ad,#4e5660);border:3px solid var(--white)}
.quote .name{font-size:18px;font-weight:500}
.quote .role{font-size:13px;color:#7a7a7a}
.quote.main .role{color:var(--white)}
.quote .text{font-size:13px;line-height:18px}
.qmark{position:absolute;font-family:'Poppins',sans-serif;font-weight:700;line-height:1}
.stars{position:absolute;left:0;width:100%;font-size:18px;letter-spacing:4px}
.stars .off{color:#9a9a9a}
.arrow{position:absolute;top:3430px;width:34px;height:34px;border-radius:50%;background:var(--red);display:flex;align-items:center;justify-content:center}

/* footer */
.site-footer{position:absolute;left:0;top:3554px;width:1200px;height:443px;background:linear-gradient(120deg,#7b0a0d 0%,#c41218 60%,#9c0d11 100%);border-radius:22px 22px 0 0;color:var(--white)}
.site-footer .brand{left:60px;top:94px;font-size:32px;color:var(--white)}
.foot-about{position:absolute;left:60px;top:161px;width:330px;font-size:13px;line-height:19px}
.payments{position:absolute;left:60px;top:265px;display:flex;gap:17px}
.payments span{width:36px;height:24px;background:var(--white);border-radius:4px}
.subscribe{position:absolute;left:608px;top:80px;font-family:'Poppins',sans-serif;font-weight:600;font-size:19px;line-height:25px}
.email{position:absolute;left:800px;top:79px;width:340px;height:41px;background:var(--white);border-radius:21px;color:var(--ink);font-size:13px;padding-left:26px;display:flex;align-items:center}
.email b{position:absolute;right:0;top:0;width:48px;height:41px;border-radius:0 21px 21px 0;background:#111;display:flex;align-items:center;justify-content:center}
.foot-col{position:absolute;top:158px}
.foot-col h4{font-family:'Poppins',sans-serif;font-weight:600;font-size:18px;margin-bottom:26px}
.foot-col a{display:block;color:var(--white);text-decoration:none;font-size:13px;margin-bottom:13px}
.foot-rule{position:absolute;left:60px;top:332px;width:1080px;height:2px;background:var(--white)}
.foot-rule::before,.foot-rule::after{content:"";position:absolute;top:-3px;width:8px;height:8px;border-radius:50%;background:var(--white)}
.foot-rule::before{left:-2px}.foot-rule::after{right:-2px}
.socials{position:absolute;left:60px;top:381px;display:flex;gap:9px}
.socials span{width:16px;height:16px;border-radius:50%;background:var(--white)}
.copyright{position:absolute;right:60px;top:383px;font-size:11px}
</style>
</head>
<body>

<header class="site-header">
  <div class="brand"><i></i>Velmora</div>
  <nav class="main-nav">
    <a class="active" href="#">Introduction</a><a href="#">Shop</a><a href="#">Products</a><a href="#">Information Etc</a>
  </nav>
  <div class="header-icons">
    <svg width="16" height="16" viewBox="0 0 16 16" fill="none" stroke="#111" stroke-width="1.6"><circle cx="7" cy="7" r="5"/><path d="M11 11l4 4"/></svg>
    <svg width="16" height="16" viewBox="0 0 16 16" fill="none" stroke="#111" stroke-width="1.4"><circle cx="8" cy="5" r="3"/><path d="M2 15c1-4 11-4 12 0"/></svg>
    <svg width="16" height="16" viewBox="0 0 16 16" fill="none" stroke="#111" stroke-width="1.4"><rect x="1.5" y="3" width="13" height="10" rx="1"/><path d="M2 4l6 5 6-5"/></svg>
  </div>
</header>

<section class="hero">
  <div class="hero-photo" role="img" aria-label="Drei Konservendosen mit Suppen und Fonds auf einem rustikalen Holztisch"></div>
  <h1>Warmth And Flavor,<br>Spoonful By Spoonful</h1>
  <p>Lorem Ipsum Dolor Sit Amet, Consectetur Adipiscing Elit, Sed Do Eiusmod Tempor Incididunt Ut Labore Et Dolore Magna Aliqua.</p>
  <span class="btn">Oder Now
    <svg width="14" height="10" viewBox="0 0 14 10" fill="none" stroke="#fff" stroke-width="1.6"><path d="M1 5h11M8 1l4 4-4 4"/></svg></span>
</section>

<h2 class="section-title" style="top:813px">Erleben Sie Jedes Mal Das Beste</h2>

<div class="card" style="left:60px;top:978px;height:267px"><div class="shot" role="img" aria-label="Suppendosen"></div><h3>Kessel-Gulasch-<br>Suppe</h3><div class="price">$8.05USD</div><div class="rule"></div><div class="more">Weitere Details ›</div></div>
<div class="card hot" style="left:334px;top:978px;height:267px"><div class="shot" role="img" aria-label="Suppendosen"></div><h3>Kessel-Gulasch-<br>Suppe</h3><div class="price">$8.05USD</div><div class="rule"></div><div class="more">Weitere Details ›</div></div>
<div class="card" style="left:607px;top:978px;height:267px"><div class="shot" role="img" aria-label="Suppendosen"></div><h3>Kessel-Gulasch-<br>Suppe</h3><div class="price">$8.05USD</div><div class="rule"></div><div class="more">Weitere Details ›</div></div>
<div class="card" style="left:881px;top:978px;height:267px"><div class="shot" role="img" aria-label="Suppendosen"></div><h3>Kessel-Gulasch-<br>Suppe</h3><div class="price">$8.05USD</div><div class="rule"></div><div class="more">Weitere Details ›</div></div>

<div class="card" style="left:60px;top:1330px;height:267px"><div class="shot" role="img" aria-label="Suppendosen"></div><h3>Kessel-Gulasch-<br>Suppe</h3><div class="price">$8.05USD</div><div class="rule"></div><div class="more">Weitere Details ›</div></div>
<div class="card" style="left:334px;top:1330px;height:267px"><div class="shot" role="img" aria-label="Suppendosen"></div><h3>Kessel-Gulasch-<br>Suppe</h3><div class="price">$8.05USD</div><div class="rule"></div><div class="more">Weitere Details ›</div></div>
<div class="card" style="left:607px;top:1330px;height:267px"><div class="shot" role="img" aria-label="Suppendosen"></div><h3>Kessel-Gulasch-<br>Suppe</h3><div class="price">$8.05USD</div><div class="rule"></div><div class="more">Weitere Details ›</div></div>
<div class="card" style="left:881px;top:1330px;height:267px"><div class="shot" role="img" aria-label="Suppendosen"></div><h3>Kessel-Gulasch-<br>Suppe</h3><div class="price">$8.05USD</div><div class="rule"></div><div class="more">Weitere Details ›</div></div>

<section class="banner">
  <div class="banner-photo" role="img" aria-label="Schale mit Tomatensuppe, Kräutern, Kirschtomaten und geriebenem Käse auf dunklem Grund"></div>
  <h2>Mit Sorgfalt Gefertigt,<br>Für Sie Gemacht</h2>
  <span class="btn">Entdecken Sie Mehr</span>
</section>

<h2 class="section-title" style="top:2152px">Wo Qualität Auf Innovation Trifft</h2>
<div class="shop-label">Geschäft</div>
<div class="tabs">
  <span class="tab">Soups</span><span class="dot-sep"><i></i><i></i></span>
  <span>Sauces</span><span class="dot-sep"><i></i><i></i></span>
  <span>Bouillons</span><span class="dot-sep"><i></i><i></i></span>
  <span>Concentrates</span>
</div>

<div class="card wide" style="left:60px;top:2430px;height:348px"><div class="shot" role="img" aria-label="Gemüsesuppe in Dosen"></div><h3>Kessel-Gulasch</h3><p class="desc">Lorem Ipsum Dolor Si Amet, Consectetur Adipiscing Elit, Sed Do Eiusmod&nbsp; Incididunt Ut Labore.</p><div class="price">$8.85</div><div class="rule"></div><div class="more">Weitere Details ›</div></div>
<div class="card wide" style="left:334px;top:2430px;height:348px"><div class="shot" role="img" aria-label="Suppenbasis in Dosen" style="background:linear-gradient(180deg,#eee 0%,#e0c23a 55%,#c8a23a 100%)"></div><h3>Kessel-Gulasch</h3><p class="desc">Lorem Ipsum Dolor Si Amet, Consectetur Adipiscing Elit, Sed Do Eiusmod&nbsp; Incididunt Ut Labore.</p><div class="price">$8.85</div><div class="rule"></div><div class="more">Weitere Details ›</div></div>
<div class="card wide hot" style="left:607px;top:2430px;height:348px"><div class="shot" role="img" aria-label="Wildfond in Dosen" style="background:linear-gradient(180deg,#eee 0%,#6a1530 55%,#c8a23a 100%)"></div><h3>Kessel-Gulasch</h3><p class="desc">Lorem Ipsum Dolor Si Amet, Consectetur Adipiscing Elit, Sed Do Eiusmod&nbsp; Incididunt Ut Labore.</p><div class="price">$8.85</div><div class="rule"></div><div class="more">Weitere Details ›</div></div>
<div class="card wide" style="left:881px;top:2430px;height:348px"><div class="shot" role="img" aria-label="Kalbsfond in Dosen" style="background:linear-gradient(180deg,#eee 0%,#9aa0a8 50%,#c2191d 100%)"></div><h3>Kessel-Gulasch</h3><p class="desc">Lorem Ipsum Dolor Si Amet, Consectetur Adipiscing Elit, Sed Do Eiusmod&nbsp; Incididunt Ut Labore.</p><div class="price">$8.85</div><div class="rule"></div><div class="more">Weitere Details ›</div></div>

<h2 class="section-title" style="top:2869px">Hauskäufer Vertrauen Darauf<br>Und Verkäufer</h2>

<div class="quote" style="left:60px;top:3177px;width:256px;height:287px">
  <div class="name" style="position:absolute;left:0;width:100%;top:56px">Jonas Keller</div>
  <div class="role" style="position:absolute;left:0;width:100%;top:82px">Project Manager</div>
  <span class="qmark" style="left:22px;top:94px;font-size:22px">“</span>
  <p class="text" style="position:absolute;left:30px;width:196px;top:120px">Lorem ipsum dolor sit amet consectetur. Velit ultricies et faucibus tortor suspendisse id auctor. Integer commodo eget at nec nisl amet. Rhoncus egestas pharetra mi ipsum.</p>
  <span class="qmark" style="right:16px;top:228px;font-size:22px">”</span>
  <div class="stars" style="top:254px">★★★★<span class="off">★</span></div>
</div>
<div class="avatar" role="img" aria-label="Porträtfoto des Kunden" style="left:146px;top:3130px;width:84px;height:84px"></div>

<div class="quote main" style="left:335px;top:3096px;width:530px;height:287px">
  <div class="name" style="position:absolute;left:0;width:100%;top:50px">Lena Hartwig</div>
  <div class="role" style="position:absolute;left:0;width:100%;top:74px">Global Directives Architect</div>
  <span class="qmark" style="left:26px;top:70px;font-size:44px">“</span>
  <p class="text" style="position:absolute;left:30px;width:470px;top:110px;font-size:14px">Lorem ipsum dolor sit amet consectetur. Velit ultricies et faucibus tortor suspendisse id auctor. Integer commodo eget at nec nisl amet. Rhoncus egestas pharetra mi ipsum. Tellus vestibulum justo nibh neque pulvinar congue. Laoreet eu placerat cursus sed nunc. Est lectus amet rhoncus ultricies augue faucibus egestas sit volutpat. Porttitor velit urna amet in dictum ut sapien.</p>
  <span class="qmark" style="right:26px;top:212px;font-size:44px">”</span>
  <div class="stars" style="top:226px">★★★★<span class="off">★</span></div>
</div>
<div class="avatar" role="img" aria-label="Porträtfoto der Kundin" style="left:558px;top:3043px;width:84px;height:84px"></div>

<div class="quote" style="left:884px;top:3177px;width:256px;height:287px">
  <div class="name" style="position:absolute;left:0;width:100%;top:56px">Mara Lindqvist</div>
  <div class="role" style="position:absolute;left:0;width:100%;top:82px">Dog Trainer</div>
  <span class="qmark" style="left:18px;top:94px;font-size:22px">“</span>
  <p class="text" style="position:absolute;left:30px;width:196px;top:120px">Lorem ipsum dolor sit amet consectetur. Velit ultricies et faucibus tortor suspendisse id auctor. Integer commodo eget at nec nisl amet. Rhoncus egestas pharetra mi ipsum.</p>
  <span class="qmark" style="right:16px;top:228px;font-size:22px">”</span>
  <div class="stars" style="top:254px">★★★★<span class="off">★</span></div>
</div>
<div class="avatar" role="img" aria-label="Porträtfoto der Kundin" style="left:970px;top:3130px;width:84px;height:84px"></div>

<span class="arrow" style="left:557px"><svg width="10" height="12" viewBox="0 0 10 12" fill="none" stroke="#fff" stroke-width="2"><path d="M7 1L2 6l5 5"/></svg></span>
<span class="arrow" style="left:608px"><svg width="10" height="12" viewBox="0 0 10 12" fill="none" stroke="#fff" stroke-width="2"><path d="M3 1l5 5-5 5"/></svg></span>

<footer class="site-footer">
  <div class="brand"><i></i>Velmora</div>
  <p class="foot-about">Lorem Ipsum Dolor Sit Amet Consectetur. Ut Nulla Pellentesque Turpis Viverra Id Amet Bibendum. Vel Porttitor Sed Lacus Mollis Ornare.</p>
  <div class="payments"><span></span><span></span><span></span><span></span><span></span></div>
  <div class="subscribe">Subscribe To<br>Our New Letter</div>
  <div class="email">Enter Your Email<b><svg width="10" height="14" viewBox="0 0 10 14" fill="none" stroke="#fff" stroke-width="2"><path d="M2 1l6 6-6 6"/></svg></b></div>
  <div class="foot-col" style="left:608px"><h4>Company</h4><a href="#">About Us</a><a href="#">Work With Us</a><a href="#">Blog &amp; News</a></div>
  <div class="foot-col" style="left:836px"><h4>Shop</h4><a href="#">Collections</a><a href="#">Blog Post</a><a href="#">Wishlist</a></div>
  <div class="foot-col" style="left:1049px"><h4>Quick Link</h4><a href="#">Shop</a><a href="#">Blog</a><a href="#">Contact</a></div>
  <div class="foot-rule"></div>
  <div class="socials"><span></span><span></span><span></span><span></span></div>
  <div class="copyright">Copyright © 2024 <b>Studio Norvale</b>. All Rights Reserved.</div>
</footer>

</body>
</html>
```